Melorix artwork for new single release

I need Melorix artwork creating to release a new single on there.

The specs are:

Ideal size: 3000 x 3000 pixels
Minimum size: 1400 x 1400 pixels
Aspect ratio: 1:1 (must be a perfect square)
File format: JPG or PNG
Color space: sRGB
File size: Max 4MB

The song is called "Was It Ever Rain?"
The artist is "Martin Hollow"

We have no images of Martin, so it really is open to imagination.

Target Market(s)

Melorix listeners

Industry/Entity Type

Music

```html
<!DOCTYPE html>
<html lang="en">
<head>
<meta charset="utf-8">
<title>Was It Ever Rain? — Martin Hollow</title>
<link rel="stylesheet" href="https://fonts.googleapis.com/css2?family=Abril+Fatface&family=Oswald:wght@400&display=swap">
<style>
  :root {
    --ink-dark: #141414;
    --ink-mid: #2a2a2a;
    --ink-soft: #3b3b3b;
    --band-deep: #2a0506;
    --band-red: #5a0a0c;
    --band-glow: #a3141a;
    --type-white: #f4f2f0;
  }
  * { margin: 0; padding: 0; box-sizing: border-box; }
  html, body {
    width: 1200px;
    height: 1200px;
    overflow: hidden;
    background: var(--ink-dark);
  }
  .cover {
    position: relative;
    width: 1200px;
    height: 1200px;
    overflow: hidden;
  }
  .portrait-backdrop {
    position: absolute;
    inset: 0;
    background:
      radial-gradient(ellipse 420px 300px at 560px 180px, var(--ink-soft), transparent 70%),
      radial-gradient(ellipse 460px 280px at 560px 1020px, var(--ink-soft), transparent 70%),
      linear-gradient(180deg, var(--ink-mid) 0%, var(--ink-dark) 50%, var(--ink-mid) 100%);
  }
  .portrait-band {
    position: absolute;
    left: 0;
    top: 400px;
    width: 1200px;
    height: 395px;
    background:
      radial-gradient(ellipse 160px 200px at 860px 620px, var(--band-glow), transparent 70%),
      radial-gradient(ellipse 120px 260px at 600px 640px, rgba(163,20,26,0.7), transparent 70%),
      linear-gradient(90deg, var(--band-deep) 0%, var(--band-red) 45%, var(--band-deep) 100%);
    background-attachment: local;
  }
  .title-line {
    position: absolute;
    left: 0;
    width: 1200px;
    text-align: center;
    color: var(--type-white);
    font-family: "Abril Fatface", "Playfair Display", serif;
    text-transform: uppercase;
    line-height: 1;
  }
  .title-top {
    top: 160px;
    font-size: 62px;
    letter-spacing: 52px;
    padding-left: 52px;
  }
  .title-main {
    top: 505px;
    font-size: 168px;
    letter-spacing: 78px;
    padding-left: 78px;
  }
  .title-bottom {
    top: 970px;
    font-size: 62px;
    letter-spacing: 40px;
    padding-left: 40px;
  }
  .artist-name {
    position: absolute;
    left: 0;
    top: 696px;
    width: 1200px;
    text-align: center;
    color: var(--type-white);
    font-family: "Oswald", "Arial Narrow", sans-serif;
    font-weight: 400;
    font-size: 30px;
    line-height: 1;
    letter-spacing: 40px;
    padding-left: 40px;
    text-transform: uppercase;
  }
</style>
</head>
<body>
  <main class="cover">
    <div class="portrait-backdrop" role="img" aria-label="Dark grainy black-and-white close-up portrait photograph of the artist"></div>
    <div class="portrait-band" role="img" aria-label="Red-tinted close-up photograph of the artist's eye across a horizontal band"></div>

    <h1 class="title">
      <span class="title-line title-top">Was It</span>
      <span class="title-line title-main">Ever</span>
      <span class="title-line title-bottom">Rain?</span>
    </h1>
    <p class="artist-name">Martin Hollow</p>
  </main>
</body>
</html>
```